Northfield Builders Guild Business card

We are looking for a new business card design with photo included.
Our business is a nonprofit construction contractor membership organization. We offer business education, assist with business setup and licensing, provide safety training, and provide a member directory.
URL: www.builderslinkguild.org
Color code:
CMYK: 0 cyan, 42 magenta, 100 yellow, 0 black for Print.
Hexidecimal: #FF9900
RGB: R 255; G 153; B 0

```html
<!DOCTYPE html>
<html lang="en">
<head>
<meta charset="utf-8">
<title>Northfield Builders Guild – Business Card</title>
<link href="https://fonts.googleapis.com/css2?family=Open+Sans:wght@400;600;700;800&family=Oswald:wght@400;500&display=swap" rel="stylesheet">
<style>
  :root {
    --orange: #f89b1f;
    --ink: #333333;
    --card: #ffffff;
    --backdrop: #e8e5e0;
  }
  * { margin: 0; padding: 0; box-sizing: border-box; }
  html, body { width: 1200px; height: 960px; overflow: hidden; }
  body {
    background: var(--backdrop);
    position: relative;
    font-family: "Open Sans", sans-serif;
    color: var(--ink);
  }
  .card {
    position: absolute;
    left: 300px;
    width: 600px;
    height: 345px;
    background: var(--card);
    overflow: hidden;
  }
  .card--front { top: 110px; }
  .card--back { top: 478px; }

  .brand {
    position: absolute;
    left: 42px;
    top: 52px;
    display: flex;
    align-items: center;
    gap: 12px;
  }
  .brand__mark {
    width: 16px;
    height: 16px;
    background: var(--orange);
    flex: none;
  }
  .brand__name {
    font-weight: 800;
    font-size: 25px;
    line-height: 1.05;
    color: var(--ink);
    letter-spacing: -0.3px;
  }

  .person {
    position: absolute;
    right: 22px;
    top: 60px;
    text-align: right;
  }
  .person__name {
    font-family: "Oswald", sans-serif;
    font-weight: 500;
    font-size: 32px;
    line-height: 1.1;
    letter-spacing: -0.5px;
    transform: scaleX(0.82);
    transform-origin: right center;
  }
  .person__title {
    font-size: 11.5px;
    margin-top: 3px;
  }

  .band {
    position: absolute;
    left: 0;
    top: 149px;
    width: 600px;
    height: 146px;
  }
  .contacts {
    position: absolute;
    left: 31px;
    top: 171px;
    list-style: none;
  }
  .contacts__item {
    display: flex;
    align-items: center;
    height: 34px;
    font-size: 16.5px;
  }
  .contacts__icon {
    width: 26px;
    height: 24px;
    margin-right: 15px;
    flex: none;
  }

  .website {
    position: absolute;
    left: 41px;
    top: 313px;
    font-size: 13px;
    letter-spacing: 3.6px;
  }

  .brand--centered {
    left: 0;
    right: 0;
    top: 128px;
    justify-content: center;
    gap: 16px;
  }
  .brand--centered .brand__mark { width: 24px; height: 24px; }
  .brand--centered .brand__name { font-size: 40px; }
</style>
</head>
<body>
  <section class="card card--front">
    <div class="brand">
      <span class="brand__mark"></span>
      <span class="brand__name">Northfield<br>Builders Guild</span>
    </div>

    <div class="person">
      <p class="person__name">DANIEL REYES</p>
      <p class="person__title">CEO/Managing Director</p>
    </div>

    <svg class="band" viewBox="0 0 600 146" aria-hidden="true">
      <polygon fill="var(--orange)" points="0,0 445,0 411,77 430,146 0,146"/>
      <polygon fill="var(--orange)" points="504,0 600,0 600,146 519,146 537,77"/>
    </svg>

    <ul class="contacts">
      <li class="contacts__item">
        <svg class="contacts__icon" viewBox="0 0 26 24" aria-hidden="true">
          <rect x="1" y="0" width="24" height="22" rx="4" fill="var(--ink)"/>
          <path d="M8 5 c-2 1 -2 4 1 8 c3 4 6 5 8 3 l-2.5 -2.5 l-1.8 1 c-1.5 -1 -3 -3 -3.5 -4.5 l1 -1.8 z" fill="var(--orange)"/>
          <path d="M15 5 a4 4 0 0 1 4 4 M15 2.8 a6.2 6.2 0 0 1 6.2 6.2" stroke="var(--orange)" stroke-width="1.3" fill="none"/>
        </svg>
        <span>555-014-2288</span>
      </li>
      <li class="contacts__item">
        <svg class="contacts__icon" viewBox="0 0 26 24" aria-hidden="true">
          <rect x="1" y="0" width="24" height="22" rx="3" fill="var(--ink)"/>
          <path d="M4 11.5 L13 4 L22 11.5" stroke="var(--orange)" stroke-width="2" fill="none"/>
          <path d="M7 11 V19 H11 V14.5 H15 V19 H19 V11" stroke="var(--orange)" stroke-width="1.8" fill="none"/>
        </svg>
        <span>555-014-2288</span>
      </li>
      <li class="contacts__item">
        <svg class="contacts__icon" viewBox="0 0 26 24" aria-hidden="true">
          <rect x="2" y="1.5" width="22" height="20" rx="3" fill="none" stroke="var(--ink)" stroke-width="2"/>
          <path d="M5 6 L13 13 L21 6 M5 17 L10.5 11.5 M21 17 L15.5 11.5" stroke="var(--ink)" stroke-width="1.4" fill="none"/>
        </svg>
        <span>d.reyes@builderslinkguild.org</span>
      </li>
    </ul>

    <p class="website">www.builderslinkguild.org</p>
  </section>

  <section class="card card--back">
    <div class="brand brand--centered">
      <span class="brand__mark"></span>
      <span class="brand__name">Northfield<br>Builders Guild</span>
    </div>
  </section>
</body>
</html>
```